Website for new dental office

I am Dr. Colin Ashford and am building a new dental practice. I specialize in general dentistry. I am young and have a higher end dental practice incorporating very new technologies and would like my website to reflect that. As many dental patients are older, the website must be very easy to navigate. I would like patients to be able to request appointments, and will eventually add on patient information forms (the health history, etc, that you normally fill out in the practice) from my practice management software, so leave an area for that.

Industry/Entity Type

Building

```html
<!DOCTYPE html>
<html lang="en">
<head>
<meta charset="utf-8">
<title>Ashford Dental – Home</title>
<link rel="stylesheet" href="https://fonts.googleapis.com/css2?family=Open+Sans:wght@400;600;700;800&display=swap">
<style>
:root{
  --blue:#3f7fcc;
  --blue-dark:#2f67ad;
  --blue-nav:#4d8ad3;
  --orange:#e9a21c;
  --ink:#333a44;
  --muted:#7d8792;
  --line:#dfe4ea;
  --page:#ffffff;
  --footer:#3b3e43;
  --footer-ink:#b9bec5;
  --field:#ffffff;
}
*{box-sizing:border-box;margin:0;padding:0}
html,body{width:1200px;height:684px;overflow:hidden;background:var(--page);font-family:"Open Sans",Arial,sans-serif;color:var(--ink)}
.site{width:1200px;height:684px;display:flex;flex-direction:column}
.wrap{width:960px;margin:0 auto;position:relative}

/* top bar */
.topbar{height:22px;font-size:10px;color:var(--muted)}
.topbar .wrap{display:flex;justify-content:flex-end;align-items:center;height:22px;gap:14px}
.social-link{display:flex;align-items:center;gap:4px}
.social-link i{width:7px;height:7px;background:var(--blue);display:inline-block}

/* header */
.header{height:64px}
.header .wrap{display:flex;align-items:center;justify-content:space-between;height:64px}
.brand{display:flex;align-items:center;gap:10px;font-size:22px;font-weight:600;color:var(--blue)}
.brand-mark{width:26px;height:26px;border-radius:50%;background:var(--blue)}
.header-right{display:flex;align-items:center;gap:22px}
.chat{display:flex;align-items:center;gap:8px}
.chat-portrait{width:40px;height:40px;border-radius:50%;background:radial-gradient(circle at 50% 40%,#f1d4be,#c9a48a 60%,#e9eef3 61%)}
.chat-text{font-size:11px;color:var(--blue);font-weight:600;line-height:1.2}
.chat-btn{display:block;margin-top:3px;background:var(--orange);color:#fff;font-size:12px;padding:3px 10px;border-radius:3px;font-weight:700}
.enquiries{font-size:12px;line-height:1.4;color:var(--ink)}
.enquiries .label{color:var(--blue);font-weight:700;font-size:10px;letter-spacing:.5px;display:flex;align-items:center;gap:4px}

/* navigation */
.nav{height:34px;background:var(--blue-nav)}
.nav ul{list-style:none;display:flex;height:34px}
.nav li{color:#fff;font-size:11px;font-weight:600;text-transform:uppercase;padding:0 22px;display:flex;align-items:center}
.nav li.active{background:var(--orange)}

/* hero */
.hero{height:200px;position:relative;background:linear-gradient(90deg,#eef2f6 0%,#e4eaf0 40%,#dfe6ee 100%)}
.hero-photo{position:absolute;right:0;top:0;width:62%;height:100%;background:linear-gradient(120deg,#f2ece4 0%,#e9c46a 30%,#f3e7da 50%,#a8b6c8 75%,#dde3ea 100%)}
.hero-copy{position:absolute;left:calc(50% - 480px);top:58px}
.hero-copy .kicker{font-size:22px;color:var(--blue);font-weight:400}
.hero-copy h1{font-size:34px;font-weight:800;color:var(--orange);line-height:1.05}
.hero-copy p{font-size:15px;color:var(--ink);margin-top:4px}

/* appointment panel */
.appointment{height:160px;position:relative}
.appointment .wrap{height:160px}
.panel{position:absolute;left:0;right:0;top:-20px;height:170px;background:var(--blue);color:#fff}
.panel-tabs{display:flex;height:30px}
.tab{flex:1;display:flex;align-items:center;gap:8px;padding-left:16px;font-size:14px;font-weight:600}
.tab-main{background:var(--blue-dark)}
.tab-emergency{background:#fff;color:var(--blue);flex:0 0 320px}
.panel-body{display:grid;grid-template-columns:1fr 1fr 1fr;gap:28px;padding:12px 16px}
.col h3{font-size:12px;font-weight:600;display:flex;align-items:center;gap:6px;margin-bottom:8px}
.hours{width:100%;border-collapse:collapse;font-size:10px}
.hours td{padding:5px 0;border-bottom:1px solid rgba(255,255,255,.35)}
.hours td:last-child{text-align:right}
.col p{font-size:10px;line-height:1.4}
.btn-light{display:inline-block;background:#fff;color:var(--blue);font-size:10px;padding:3px 12px;border-radius:2px;margin-top:10px}
.form{display:grid;grid-template-columns:1fr 1fr;gap:8px}
.field{background:transparent;border:1px solid rgba(255,255,255,.7);color:#fff;font-size:9px;padding:4px 6px}
.form .send{grid-column:2;justify-self:end;background:#fff;color:var(--blue);font-size:10px;padding:3px 18px;border-radius:2px}

/* services */
.services-title{height:36px}
.services-title h2{font-size:13px;font-weight:400;color:var(--ink);padding-top:10px;display:inline-block;border-bottom:2px solid var(--orange);padding-bottom:2px}
.services-title h2 strong{color:var(--orange);font-weight:700;text-transform:uppercase}
.tiles{height:96px}
.tiles .wrap{display:grid;grid-template-columns:repeat(4,1fr);gap:4px;height:96px}
.tile{display:flex;flex-direction:column}
.tile-photo{height:48px}
.tile-photo.smile{background:linear-gradient(135deg,#e7b9a8,#f6f1ee 55%,#c98c7f)}
.tile-photo.whitening{background:linear-gradient(135deg,#d8a598,#fbf7f3 50%,#b97c72)}
.tile-photo.implants{background:linear-gradient(135deg,#c7d0d8,#eef1f4 50%,#9aa6b2)}
.tile-photo.kids{background:linear-gradient(135deg,#e9d2c0,#f7efe7 50%,#b3c5d8)}
.tile-caption{flex:1;background:var(--blue);color:#fff;padding:5px 8px}
.tile-caption h4{font-size:11px;font-weight:700}
.tile-caption p{font-size:9px;opacity:.9}

.partners{height:36px}
.partners .wrap{display:flex;align-items:center;justify-content:space-around;height:36px}
.badge{width:90px;height:18px;border-radius:3px;background:#d6dde5}

/* footer */
.footer{height:36px;background:var(--footer);color:var(--footer-ink);font-size:10px}
.footer .wrap{display:flex;align-items:center;justify-content:space-between;height:36px}
.footer strong{color:#fff;font-weight:600;margin-right:16px}
.footer span{margin-right:14px}
</style>
</head>
<body>
<div class="site">
  <div class="topbar">
    <div class="wrap">
      <span class="social-link"><i></i>Community</span>
      <span class="social-link"><i></i>Updates</span>
      <span class="social-link"><i></i>Network</span>
      <span class="social-link"><i></i>Circle</span>
    </div>
  </div>

  <header class="header">
    <div class="wrap">
      <div class="brand"><span class="brand-mark"></span>Ashford Dental</div>
      <div class="header-right">
        <div class="chat">
          <div class="chat-portrait" role="img" aria-label="Photo of a smiling receptionist with headset"></div>
          <div class="chat-text">Have Questions?<span class="chat-btn">Chat Online</span></div>
        </div>
        <div class="enquiries">
          <div class="label">
            <svg width="10" height="10" viewBox="0 0 24 24" fill="currentColor"><path d="M6.6 10.8a15.1 15.1 0 0 0 6.6 6.6l2.2-2.2a1 1 0 0 1 1-.25 11.4 11.4 0 0 0 3.6.6 1 1 0 0 1 1 1V20a1 1 0 0 1-1 1A17 17 0 0 1 3 4a1 1 0 0 1 1-1h3.5a1 1 0 0 1 1 1c0 1.25.2 2.45.6 3.6a1 1 0 0 1-.25 1z"/></svg>
            ENQUIRIES
          </div>
          <div>Call: 555 018 22</div>
          <div>Intl: +12 3 555 0199</div>
        </div>
      </div>
    </div>
  </header>

  <nav class="nav">
    <div class="wrap">
      <ul>
        <li class="active">Home</li>
        <li>About Us</li>
        <li>The Practice</li>
        <li>Area of Expertise</li>
        <li>Appointment</li>
        <li>Contact</li>
      </ul>
    </div>
  </nav>

  <section class="hero">
    <div class="hero-photo" role="img" aria-label="Photo of a smiling family: mother, father and young daughter"></div>
    <div class="hero-copy">
      <div class="kicker">We Care About</div>
      <h1>PROIN GRAVIDA NIBH</h1>
      <p>Lorem quis bibendum auctor, nisi elit</p>
    </div>
  </section>

  <section class="appointment">
    <div class="wrap">
      <div class="panel">
        <div class="panel-tabs">
          <div class="tab tab-main">Make an Appointment</div>
          <div class="tab tab-emergency">
            <svg width="14" height="14" viewBox="0 0 24 24" fill="currentColor"><rect x="2" y="6" width="20" height="14" rx="2"/><rect x="8" y="3" width="8" height="4" rx="1"/><circle cx="12" cy="13" r="4" fill="#fff"/></svg>
            For Emergency Cases
          </div>
        </div>
        <div class="panel-body">
          <div class="col">
            <h3><svg width="12" height="12" viewBox="0 0 24 24" fill="none" stroke="#fff" stroke-width="2.5"><circle cx="12" cy="12" r="9"/><path d="M12 7v5l3 2"/></svg>Working Time</h3>
            <table class="hours">
              <tr><td>Monday – Friday</td><td>8.00 – 17.00</td></tr>
              <tr><td>Saturday</td><td>9.30 – 17.30</td></tr>
              <tr><td>Sunday</td><td>9.30 – 15.00</td></tr>
            </table>
          </div>
          <div class="col">
            <h3><svg width="12" height="12" viewBox="0 0 24 24" fill="none" stroke="#fff" stroke-width="2.5"><rect x="3" y="5" width="18" height="16" rx="1"/><path d="M3 10h18M8 3v4M16 3v4"/></svg>Doctors Timetable</h3>
            <p>Lorem ipsum dolor sit amet, consectetur adipisicing elit, sed do eiusmod tempor incididunt ut labore et dolore.</p>
            <span class="btn-light">View Timetable</span>
          </div>
          <div class="col">
            <h3><svg width="12" height="12" viewBox="0 0 24 24" fill="none" stroke="#fff" stroke-width="2.5"><rect x="3" y="5" width="18" height="16" rx="1"/><path d="M3 10h18M8 3v4M16 3v4M9 15l2 2 4-4"/></svg>Booking a Visit</h3>
            <div class="form">
              <span class="field">Select Department</span>
              <span class="field">Your Phone</span>
              <span class="field">Full Name</span>
              <span class="field">mm/dd/yyyy</span>
              <span class="send">Send</span>
            </div>
          </div>
        </div>
      </div>
    </div>
  </section>

  <section class="services-title">
    <div class="wrap"><h2>About <strong>Our Services</strong></h2></div>
  </section>

  <section class="tiles">
    <div class="wrap">
      <article class="tile">
        <div class="tile-photo smile" role="img" aria-label="Close-up photo of a bright smile"></div>
        <div class="tile-caption"><h4>Cosmetic Dentistry</h4><p>Natural looking results for every smile.</p></div>
      </article>
      <article class="tile">
        <div class="tile-photo whitening" role="img" aria-label="Close-up photo of white teeth"></div>
        <div class="tile-caption"><h4>Teeth Whitening</h4><p>Brighter teeth in a single visit.</p></div>
      </article>
      <article class="tile">
        <div class="tile-photo implants" role="img" aria-label="Photo of a dental implant model"></div>
        <div class="tile-caption"><h4>Dental Implants</h4><p>Lasting replacements for missing teeth.</p></div>
      </article>
      <article class="tile">
        <div class="tile-photo kids" role="img" aria-label="Photo of a child at a dental check-up"></div>
        <div class="tile-caption"><h4>Kids Dentistry</h4><p>Comfortable care for young patients.</p></div>
      </article>
    </div>
  </section>

  <section class="partners">
    <div class="wrap">
      <span class="badge"></span><span class="badge"></span><span class="badge"></span><span class="badge"></span>
    </div>
  </section>

  <footer class="footer">
    <div class="wrap">
      <div><strong>Contact Information</strong><span>14 Linden Street, Westbrook</span><span>Tel: 555 018 2240</span><span>hello@ashforddental.example</span></div>
      <div><span>Privacy Policy</span><span>Terms of Use</span><span>© 2024 Ashford Dental</span></div>
    </div>
  </footer>
</div>
</body>
</html>
```